A Modern & Sleek "Coming Soon" Page for an A.I Recruiting App

For the “Coming Soon” website, a simple background with no people in it. I've attached an A.I image of what the page should generally look like.

- A single mobile phone as the main focus where the user actually clicks on the, “notify me” button (after entering their email address).
- In the background where the pillars/columns are seen in the example, should be subtle pad locks that are in their opened position with a key inside the lock. I've attached images to try to illustrate this idea, but they are far away in style from what I'm looking for.

SLOGAN: Unlocking the power of meaningful connections
LOGO/TITLE: Should be the name as shown in image with only the name "KelvoLink" on it
COLORS: Purplish/blue hues. Should not be too feminine
NOTE: The user should only click once when signing up/entering their email.

Product: A recruiting platform that matches employers/employees with A.I. and prioritizing cultural fit/values system before skills. The industry we are tackling first is the caregiving industry (nannies, tutors, elderly). All users will be background screened and that info lives on the blockchain. All users will have the option to review and be reviewed/rated.

```html
<!DOCTYPE html>
<html lang="en">
<head>
<meta charset="UTF-8">
<title>KelvoLink — Coming Soon</title>
<link href="https://fonts.googleapis.com/css2?family=Orbitron:wght@400;600;700&display=swap" rel="stylesheet">
<style>
  :root {
    --bg-deep: #07074d;
    --bg-mid: #0f0f9c;
    --bg-glow: #2a1fc4;
    --ink: #ffffff;
    --phone-dark: #1a0f3a;
    --phone-violet: #5b3a9e;
    --lock-violet: #4a2ab8;
    --lock-glow: #6a3cff;
  }
  * { margin: 0; padding: 0; box-sizing: border-box; }
  html, body { width: 1200px; height: 667px; overflow: hidden; }
  body {
    font-family: "Orbitron", sans-serif;
    color: var(--ink);
    background: var(--bg-deep);
  }
  .page {
    position: relative;
    width: 1200px;
    height: 667px;
    overflow: hidden;
    background:
      radial-gradient(ellipse 70% 80% at 62% 40%, var(--bg-glow) 0%, var(--bg-mid) 40%, var(--bg-deep) 100%);
  }
  .lock-art {
    position: absolute;
    left: 523px; top: 34px;
    width: 514px; height: 566px;
    border-radius: 40px;
    background:
      radial-gradient(ellipse 45% 30% at 40% 18%, rgba(106,60,255,0.35), transparent 70%),
      radial-gradient(ellipse 55% 40% at 45% 45%, rgba(74,42,184,0.55), transparent 75%),
      radial-gradient(ellipse 25% 25% at 80% 80%, rgba(106,60,255,0.3), transparent 75%);
    opacity: 0.9;
  }
  .phone-art {
    position: absolute;
    left: 129px; top: 137px;
    width: 308px; height: 506px;
    border-radius: 42px;
    background: linear-gradient(165deg, var(--phone-violet) 0%, #3d2570 45%, var(--phone-dark) 100%);
    transform: rotate(-8deg);
    box-shadow: 0 20px 40px rgba(0,0,0,0.45);
  }
  .site-header .brand {
    position: absolute;
    left: 111px; top: 44px;
    font-weight: 400;
    font-size: 46px;
    letter-spacing: 4px;
    line-height: 1;
  }
  .menu-toggle {
    position: absolute;
    left: 862px; top: 63px;
    width: 22px; height: 18px;
  }
  .btn-outline {
    position: absolute;
    display: flex; align-items: center; justify-content: center;
    border: 1px solid var(--ink);
    color: var(--ink);
    font-weight: 700;
    text-decoration: none;
    letter-spacing: 0.5px;
  }
  .btn-signup {
    left: 939px; top: 42px;
    width: 149px; height: 59px;
    font-size: 19px;
  }
  .hero {
    position: absolute;
    left: 536px; top: 220px;
  }
  .hero .eyebrow {
    font-weight: 700;
    font-size: 28px;
    letter-spacing: 0.5px;
    line-height: 1;
  }
  .hero .slogan {
    margin-top: 44px;
    font-weight: 600;
    font-size: 33px;
    line-height: 70px;
    letter-spacing: 1px;
    white-space: nowrap;
  }
  .btn-notify {
    left: 537px; top: 467px;
    width: 183px; height: 66px;
    font-size: 20px;
  }
</style>
</head>
<body>
<main class="page">
  <div class="lock-art" role="img" aria-label="Open padlock with a circuit-pattern key, glowing in violet"></div>
  <div class="phone-art" role="img" aria-label="Smartphone showing the KelvoLink coming soon screen with a notify me button"></div>

  <header class="site-header">
    <div class="brand">KELVOLINK</div>
    <svg class="menu-toggle" viewBox="0 0 22 18" aria-label="Menu">
      <rect x="0" y="1" width="22" height="2.5" fill="#fff"/>
      <rect x="0" y="7.75" width="22" height="2.5" fill="#fff"/>
      <rect x="0" y="14.5" width="22" height="2.5" fill="#fff"/>
    </svg>
    <a class="btn-outline btn-signup" href="#">SIGN UP</a>
  </header>

  <section class="hero">
    <h2 class="eyebrow">KELVOLINK</h2>
    <h1 class="slogan">UNLOCKING THE POWER OF<br>MEANINGFUL CONNECTIONS</h1>
  </section>
  <a class="btn-outline btn-notify" href="#">NOTIFY ME</a>
</main>
</body>
</html>
```